Business Card Design for Software Development Company

I am looking for a business card design the incorporates my new logo (attached below).

Key information to include:
Name: Martin Quelbrook
Title: CEO
Email: martin@brightwellcivic.example
Phone: 555-218-9403
Website: www.brightwellcivic.example

NOTE: This design should be easy to edit so that we can order cards for different members of our team.

```html
<!DOCTYPE html>
<html lang="en">
<head>
<meta charset="utf-8">
<title>Brightwell Studio Business Card</title>
<link href="https://fonts.googleapis.com/css2?family=Montserrat:wght@400;500;700&display=swap" rel="stylesheet">
<style>
  :root {
    --bg: #d9d8d6;
    --card-white: #ffffff;
    --card-dark: #232323;
    --teal: #17a89a;
    --orange: #e8762d;
    --peach: #f4b27a;
    --ink: #333333;
    --white: #ffffff;
  }
  * { margin: 0; padding: 0; box-sizing: border-box; }
  html, body {
    width: 1200px; height: 801px; overflow: hidden;
    background: var(--bg);
    font-family: "Montserrat", Arial, sans-serif;
  }
  .stage { position: relative; width: 1200px; height: 801px; }

  /* Front (portrait) */
  .card-front {
    position: absolute; left: 110px; top: 110px;
    width: 330px; height: 578px;
    background: var(--card-white);
    border-bottom: 5px solid var(--teal);
    box-shadow: 0 10px 24px rgba(0,0,0,.18);
    display: flex; flex-direction: column;
  }
  .front-info {
    flex: 1; display: flex; flex-direction: column; align-items: center;
    padding-top: 120px; text-align: center;
  }
  .person-name { font-weight: 700; font-size: 24px; letter-spacing: 1px; text-transform: uppercase; white-space: nowrap; }
  .person-name .first { color: var(--teal); }
  .person-name .last { color: var(--orange); }
  .person-title { margin-top: 4px; font-size: 18px; color: var(--ink); font-weight: 400; }
  .contact-icons { display: flex; gap: 10px; margin: 18px 0 22px; }
  .contact-icons svg { width: 24px; height: 24px; }
  .contact-list { list-style: none; font-size: 15px; color: var(--ink); line-height: 1.9; letter-spacing: .3px; }

  .front-band {
    height: 132px; background: var(--card-dark);
    display: flex; align-items: center; justify-content: center;
  }
  .front-band .brand { transform: rotate(180deg); }

  /* Brand name */
  .brand { display: flex; align-items: center; gap: 12px; color: var(--white); }
  .brand-mark { width: 14px; height: 14px; background: var(--orange); flex: none; }
  .brand-name { font-weight: 500; font-size: 26px; letter-spacing: 1px; line-height: 1; white-space: nowrap; }

  /* Back (landscape) */
  .card-back {
    position: absolute; left: 520px; top: 235px;
    width: 580px; height: 331px;
    background: var(--card-dark);
    border-bottom: 5px solid var(--teal);
    box-shadow: 0 10px 24px rgba(0,0,0,.22);
    display: flex; align-items: center; justify-content: center;
  }
  .card-back .brand { gap: 18px; }
  .card-back .brand-mark { width: 24px; height: 24px; }
  .card-back .brand-name { font-size: 44px; letter-spacing: 1.5px; }
</style>
</head>
<body>
<main class="stage">
  <section class="card-front" aria-label="Business card front">
    <div class="front-info">
      <h1 class="person-name"><span class="first">Martin</span> <span class="last">Quelbrook</span></h1>
      <p class="person-title">CEO</p>
      <div class="contact-icons" aria-hidden="true">
        <svg viewBox="0 0 24 24" class="icon-phone"><circle cx="12" cy="12" r="11" fill="var(--peach)"/><path d="M8.5 6.5c.6-.3 1.2 0 1.5.6l.8 1.7c.2.5.1 1-.3 1.3l-.7.6c.7 1.5 1.8 2.6 3.3 3.3l.6-.7c.3-.4.8-.5 1.3-.3l1.7.8c.6.3.9.9.6 1.5-.6 1.4-2 2-3.4 1.5-3.2-1.1-5.7-3.6-6.8-6.8-.5-1.4.1-2.8 1.4-3.5z" fill="#fff"/></svg>
        <svg viewBox="0 0 24 24" class="icon-mail"><circle cx="12" cy="12" r="11" fill="var(--teal)"/><rect x="6.5" y="8" width="11" height="8" rx="1" fill="#fff"/><path d="M6.8 8.4 12 12.5l5.2-4.1" stroke="var(--teal)" stroke-width="1.2" fill="none"/></svg>
        <svg viewBox="0 0 24 24" class="icon-web"><circle cx="12" cy="12" r="11" fill="var(--orange)"/><circle cx="12" cy="12" r="5.5" fill="none" stroke="#fff" stroke-width="1.3"/><ellipse cx="12" cy="12" rx="2.3" ry="5.5" fill="none" stroke="#fff" stroke-width="1.1"/><path d="M6.5 12h11" stroke="#fff" stroke-width="1.1"/></svg>
      </div>
      <ul class="contact-list">
        <li class="contact-phone">555-218-9403</li>
        <li class="contact-email">martin@brightwellcivic.example</li>
        <li class="contact-web">www.brightwellcivic.example</li>
      </ul>
    </div>
    <div class="front-band">
      <div class="brand">
        <span class="brand-mark"></span>
        <span class="brand-name">Brightwell Studio</span>
      </div>
    </div>
  </section>

  <section class="card-back" aria-label="Business card back">
    <div class="brand">
      <span class="brand-mark"></span>
      <span class="brand-name">Brightwell Studio</span>
    </div>
  </section>
</main>
</body>
</html>
```